A Brochure to sell LED Downlights to clients

I am starting a campaign on google for LED down lights the link to the landing page can be found at brinholt.com.au/led .

When the client send a contact request i want to be able to send back a brochure of a picture of each light (Approx 6 - 8 types) and have a few sentences on each light and price brake down.

'Quarnel Ostrava 9w LED'

**Information**

1-10 lights $49
11-20 lights $45
21 - 40 lights $42
40 and over $40

EACH LIGHT:

Hi,

This is very good.

I
But,

Each light will have its own price.

Can i get it made like this;

Picture - Spec - Pricing in a table style please? - i like the layout it just need to suit the tables under:

picture - Brand - Price 1-10
Model - Price 11-20
Watts - Price 21-21
lumen - price 30- 40
Warranty = price 40+

Model - Price 11-20
Watts - Price 21-21
lumen - price 30- 40
Warranty = price 40+

Model - Price 11-20
Watts - Price 21-21
lumen - price 30- 40
Warranty = price 40+

and so on....

I want it to be on Microsoft Word so i can easily chop and edit the prices and images also. (So i can print to PDF)

For more information see my website to seek inspiration. I have a zip file of my logo for actual creation and should be also to source pictures of the lights when finalising the design.

brinholt.com.au

Thanks

Added 2 x additional Dimmers please see zip file, same layout/pricing as the downlights

Target Market(s)

Homeowners/commercial business owners

Industry/Entity Type

Electric Company

Font styles to use
Sans Serif

Colors
86cfc6
ffffff
000000

Requirements
Must have
• Professional looking, Colours to the theme of my logo/website
Nice to have
• An awesome design that sells it's self!!!!!!!
• My Logo font is 'Radikil" it would be nice to follow that theme if it doesn't look good i am open to have a nice legible font for the copy.
Should not have
• Cheesy light globes or images

```html
<!DOCTYPE html>
<html lang="en">
<head>
<meta charset="utf-8">
<title>Brinholt Electrical – LED Downlight Catalog</title>
<link rel="stylesheet" href="https://fonts.googleapis.com/css2?family=Jost:wght@400;500;600;700&display=swap">
<style>
  :root {
    --stage: #333333;
    --teal: #10a89a;
    --teal-deep: #0b9a8c;
    --ink: #4a4a4a;
    --ink-dark: #3a3a3a;
    --paper: #f4f4f4;
    --white: #ffffff;
    --rule: #8a8a8a;
  }
  * { margin: 0; padding: 0; box-sizing: border-box; }
  html, body {
    width: 1200px; height: 2980px; overflow: hidden;
    background: var(--stage);
    font-family: "Jost", "Futura", sans-serif;
  }
  .page {
    position: absolute; left: 290px; width: 622px; height: 879px;
    overflow: hidden; background: var(--paper);
  }
  .abs { position: absolute; }

  /* Cover */
  .cover { top: 97px; }
  .cover-backdrop {
    inset: 0;
    background: linear-gradient(180deg, #efeeee 0%, #f7f5f3 45%, #ebe7e4 75%, #f3f1ef 100%);
  }
  .cover-title {
    right: 28px; top: 112px; text-align: right; line-height: 1;
  }
  .cover-title .word { color: var(--teal); font-size: 52px; font-weight: 400; letter-spacing: 1px; }
  .cover-title .years { color: var(--ink); font-size: 48px; font-weight: 400; margin-top: 4px; display: block; }
  .tile { position: absolute; }
  .tile-dark { left: 134px; top: 252px; width: 178px; height: 170px; background: #555555; }
  .photo-kitchen { left: 318px; top: 252px; width: 304px; height: 170px;
    background: linear-gradient(135deg, #6b4128 0%, #a8774f 45%, #d8b68a 70%, #5a3620 100%); }
  .photo-boardroom { left: 0; top: 428px; width: 126px; height: 174px;
    background: linear-gradient(160deg, #3a3126 0%, #8a6b45 45%, #2b2520 100%); }
  .photo-dining { left: 132px; top: 428px; width: 180px; height: 174px;
    background: linear-gradient(150deg, #c9b08a 0%, #8e5f3a 50%, #e2d3bd 100%); }
  .tile-brand { left: 318px; top: 428px; width: 180px; height: 174px; background: var(--teal);
    display: flex; align-items: center; justify-content: center; }
  .brand {
    color: var(--white); font-weight: 500; text-align: center; line-height: 1;
    display: flex; flex-direction: column; align-items: center;
  }
  .brand .mark { width: 14px; height: 14px; background: var(--white); margin-bottom: 10px; }
  .brand .name { font-size: 34px; }
  .brand .sub { font-size: 12px; letter-spacing: 3px; margin-top: 4px; }
  .cover-url {
    left: 0; width: 622px; top: 814px; text-align: center;
    font-size: 25px; color: var(--ink); letter-spacing: 1.5px; font-weight: 500;
  }

  /* Product page */
  .products { top: 1071px; }
  .products-backdrop {
    inset: 0;
    background: linear-gradient(180deg, #f1f1f1 0%, #e4e4e4 40%, #ececec 70%, #f5f5f5 100%);
  }
  .products-title {
    left: 0; width: 622px; top: 24px; text-align: center;
    color: var(--teal); font-weight: 700; font-size: 35px; line-height: 43px; letter-spacing: 0.5px;
  }
  .product-shot { width: 170px; height: 150px; border-radius: 50%;
    background: radial-gradient(circle at 50% 45%, #ffffff 0%, #dcdcdc 45%, #8c8c8c 75%, rgba(0,0,0,0) 76%); }
  .shot-dark { background: radial-gradient(circle at 50% 45%, #9a9a9a 0%, #4a4a4a 45%, #1e1e1e 72%, rgba(0,0,0,0) 74%); }
  .shot-satin { background: radial-gradient(circle at 50% 45%, #e8e4da 0%, #b9b3a4 45%, #7a7466 73%, rgba(0,0,0,0) 75%); }
  .product-name { color: var(--teal); font-size: 22px; font-weight: 500; }
  .features { list-style: none; }
  .features li {
    position: relative; padding-left: 18px; height: 23px;
    font-size: 11.5px; color: var(--ink); line-height: 23px;
  }
  .features li::before {
    content: ""; position: absolute; left: -2px; top: 6px; width: 11px; height: 11px;
    border-radius: 50%; background: var(--teal);
  }
  .price-panel {
    left: 26px; top: 718px; width: 580px; height: 118px;
    background: var(--ink-dark); border: 3px solid var(--teal); border-radius: 18px;
  }
  .price-label {
    left: 188px; top: 704px; width: 250px; height: 28px;
    background: var(--teal); color: var(--white);
    font-size: 17px; font-weight: 500; text-align: center; line-height: 28px;
  }
  .price-table { border-collapse: collapse; color: var(--white); font-size: 21px; }
  .price-table td { height: 32px; padding: 0; }
  .price-table .qty { width: 158px; }
  .price-table .amt { color: var(--teal); }
  .products-url { right: 28px; top: 846px; font-size: 16px; color: var(--ink); }

  /* Back cover */
  .back { top: 2025px; background: var(--teal); }
  .back-strip { left: 0; top: 0; width: 622px; height: 16px; background: var(--rule); }
  .back-backdrop {
    left: 0; top: 16px; width: 622px; height: 863px;
    background: linear-gradient(180deg, #14b0a2 0%, #0fa597 45%, #0b978a 75%, #0e9f91 100%);
  }
  .back-brand { left: 0; width: 622px; top: 276px; display: flex; justify-content: center; }
  .back-brand .name { font-size: 38px; }
  .back-brand .sub { font-size: 13px; }
  .back-url {
    left: 0; width: 622px; top: 824px; text-align: center;
    color: var(--white); font-size: 24px; font-weight: 500; letter-spacing: 1.5px;
  }
</style>
</head>
<body>

<!-- Front cover -->
<section class="page cover">
  <div class="abs cover-backdrop" role="img" aria-label="Faded photo of a bright kitchen with recessed ceiling downlights"></div>
  <h1 class="abs cover-title"><span class="word">CATALOG</span><span class="years">2017-2018</span></h1>
  <div class="tile tile-dark"></div>
  <div class="tile photo-kitchen" role="img" aria-label="Photo of a timber kitchen lit by downlights"></div>
  <div class="tile photo-boardroom" role="img" aria-label="Photo of a boardroom with ceiling downlights"></div>
  <div class="tile photo-dining" role="img" aria-label="Photo of a dining area and kitchen with downlights"></div>
  <div class="tile tile-brand">
    <div class="brand"><span class="mark"></span><span class="name">brinholt</span><span class="sub">Electrical</span></div>
  </div>
  <p class="abs cover-url">www.brinholt.com.au</p>
</section>

<!-- Product page -->
<section class="page products">
  <div class="abs products-backdrop" role="img" aria-label="Faded photo of a living room interior"></div>
  <h2 class="abs products-title">CHOOSE YOUR STYLE OF<br>LED DOWNLIGHTS</h2>

  <div class="abs product-shot" style="left:38px; top:102px;" role="img" aria-label="White LED downlight product photo"></div>
  <div class="abs product-shot" style="left:378px; top:102px;" role="img" aria-label="White LED downlight with driver product photo"></div>
  <div class="abs product-shot shot-dark" style="left:38px; top:400px;" role="img" aria-label="Black gimbal LED downlight with driver product photo"></div>
  <div class="abs product-shot shot-satin" style="left:378px; top:400px;" role="img" aria-label="Satin chrome LED downlight product photo"></div>

  <div class="abs" style="left:50px; top:260px;">
    <h3 class="product-name">Lorem ipsum dolor</h3>
    <ul class="features" style="margin-top:2px;">
      <li>Save 80% on your energy bills with LEDs</li>
      <li>50,000 hours of life</li>
      <li>Up to 7 years manufacturer's warranty</li>
      <li>Brighter than halogen downlights</li>
    </ul>
  </div>
  <div class="abs" style="left:382px; top:260px;">
    <h3 class="product-name">Lorem ipsum dolor</h3>
    <ul class="features" style="margin-top:2px;">
      <li>Save 80% on your energy bills with LEDs</li>
      <li>50,000 hours of life</li>
      <li>Up to 7 years manufacturer's warranty</li>
      <li>Brighter than halogen downlights</li>
    </ul>
  </div>
  <div class="abs" style="left:50px; top:560px;">
    <h3 class="product-name">Lorem ipsum dolor</h3>
    <ul class="features" style="margin-top:2px;">
      <li>Save 80% on your energy bills with LEDs</li>
      <li>50,000 hours of life</li>
      <li>Up to 7 years manufacturer's warranty</li>
      <li>Brighter than halogen downlights</li>
    </ul>
  </div>
  <div class="abs" style="left:382px; top:560px;">
    <h3 class="product-name">Lorem ipsum dolor</h3>
    <ul class="features" style="margin-top:2px;">
      <li>Save 80% on your energy bills with LEDs</li>
      <li>50,000 hours of life</li>
      <li>Up to 7 years manufacturer's warranty</li>
      <li>Brighter than halogen downlights</li>
    </ul>
  </div>

  <div class="abs price-panel"></div>
  <div class="abs price-label">Quarnel Ostrava 9w LED</div>
  <table class="abs price-table" style="left:64px; top:746px;">
    <tr><td class="qty">1-10......lights :</td><td class="amt">$49</td></tr>
    <tr><td class="qty">11-20...lights :</td><td class="amt">$45</td></tr>
  </table>
  <table class="abs price-table" style="left:380px; top:746px;">
    <tr><td class="qty">21-40...lights :</td><td class="amt">$42</td></tr>
    <tr><td class="qty">40 and over :</td><td class="amt">$40</td></tr>
  </table>
  <p class="abs products-url">www.brinholt.com.au</p>
</section>

<!-- Back cover -->
<section class="page back">
  <div class="abs back-strip"></div>
  <div class="abs back-backdrop" role="img" aria-label="Teal-tinted photo of a bedroom with ceiling downlights"></div>
  <div class="abs back-brand">
    <div class="brand"><span class="mark"></span><span class="name">brinholt</span><span class="sub">Electrical</span></div>
  </div>
  <p class="abs back-url">www.brinholt.com.au</p>
</section>

</body>
</html>
```